Maple Beacon Website

We are starting a marketing company and to do that we need a website! We want a website that will inspire and persuade to bring out the awesomeness in our clients.
What we want to see:
- Inspirational and persuasive imagery that relate to Branding.
- No cliche images eg. business man, suits and hand shakes
- We want to transform and educate our clients.
- We want to show them the path and would like our website to really act as a guide that guides them step by step through our process.
- We want the portray that we are an investment but not have a pretentious way to it. We put our heart into every project and that is how we treat our clients.
-When you submit your design please include what platform you have created for. Preference would be Wordpress or Joobla.

We have included the psd file for the wire frame, logo files, font files, site map and a link to a video we create to give you more information on what we would like to see. http://clipvault.example/t/qk82LmZpr

Feel free to make small modification to the logos if you think it will improve it. Your creativity and advice is most welcome.
Updates

One thing we forgot. We would like to have our contact information near the top of the website as well as at the bottom.  Here is out contact info:

Email: info@maplebeacon.example
Phone: 587-555-0142

Project Deadline Extended
Reason: As we are new with the platform and that we want to optimize our results, we decided to extend the deadline by 15 days. Thanks!

Target Market(s)

28-60, Male and Female, Oil field, Local Businesses, Dentists, Chiropractors, Hair salon, Construction/Renovation, Events etc

Industry/Entity Type

Investment

Requirements
Must have
• - 4 Inspirational and persuasive Imagery for the top portion of the website
- Must have a feel as if your not on a website an example of this is linked below.
http://www.artbidhub.example/design/402957/web-design-by-lena-torvik
Nice to have
• - Creative advice from you.
- Creative buttons for Get Free Quote and Subscribe buttons. Something out of the box that draws peoples attention. eg. a 'B' button. Just and example but still something related to branding.
Should not have
• No Cliches

```html
<!DOCTYPE html>
<html lang="en">
<head>
<meta charset="utf-8">
<title>Maple Beacon</title>
<link href="https://fonts.googleapis.com/css2?family=Open+Sans:wght@400;600;700&family=Signika:wght@600;700&display=swap" rel="stylesheet">
<style>
  :root {
    --bar-dark: #3d3f39;
    --bar-mid: #6b6d63;
    --green: #6a9a1f;
    --green-light: #8cc63f;
    --green-btn: #4a8a1e;
    --text: #5b5b5b;
    --heading: #2e2e2e;
    --page: #f7f7f7;
    --panel: #e4e4e4;
    --white: #ffffff;
  }
  * { box-sizing: border-box; margin: 0; padding: 0; }
  html, body { width: 1200px; height: 1113px; overflow: hidden; background: var(--page); }
  body { font-family: "Open Sans", sans-serif; color: var(--text); }
  .canvas { position: relative; width: 1200px; height: 1113px; overflow: hidden; background: var(--page); }

  .topbar {
    position: absolute; left: 0; top: 0; width: 1200px; height: 42px;
    background: linear-gradient(#8a8c80, var(--bar-dark));
    color: var(--white); font-size: 17px;
    display: flex; align-items: center; justify-content: flex-end; padding-right: 18px; gap: 6px;
  }
  .contact-line { display: flex; align-items: center; gap: 6px; }
  .contact-line strong { font-weight: 700; }
  .contact-line svg { fill: currentColor; }

  .hero {
    position: absolute; left: 0; top: 42px; width: 1200px; height: 380px;
    background: radial-gradient(ellipse at 58% 45%, #b9ad98 0%, #8f877a 40%, #a6a394 70%, #cfccbf 100%);
  }
  .brand-panel {
    position: absolute; left: 118px; top: 42px; width: 230px; height: 310px;
    background: linear-gradient(#ffffff 0%, #f2f2f2 45%, rgba(230,230,230,0.7) 75%, rgba(200,200,200,0) 100%);
  }
  .brand { position: absolute; left: 16px; top: 24px; display: flex; align-items: center; gap: 8px; }
  .brand-mark { width: 22px; height: 22px; background: #7c7e75; }
  .brand-name { font-family: "Open Sans", sans-serif; font-weight: 700; font-size: 22px; color: #5e6058; }
  .brand-tag { position: absolute; left: 44px; top: 78px; font-size: 13px; font-style: italic; font-weight: 600; color: #333; }
  .main-nav { position: absolute; left: 17px; top: 128px; list-style: none; }
  .main-nav li { font-weight: 700; font-size: 16px; color: #333; height: 37.5px; letter-spacing: 0.3px; }

  .steps { position: absolute; right: 18px; top: 112px; list-style: none; text-align: right; }
  .steps li {
    font-family: "Signika", sans-serif; font-weight: 700; font-size: 18px; color: #2a2a2a;
    height: 68.5px; display: flex; align-items: flex-start; justify-content: flex-end; gap: 6px;
  }
  .steps li::after {
    content: ""; width: 17px; height: 17px; border-radius: 50%; margin-top: 3px;
    background: radial-gradient(circle at 35% 30%, #e0e0e0, #6d6d6d);
  }
  .steps li.active { color: var(--green); }
  .steps li.active::after { background: radial-gradient(circle at 35% 30%, #d8f0a8, var(--green-light)); }

  .hero-caption {
    position: absolute; left: 512px; top: 365px; width: 420px; text-align: center;
    color: var(--white); font-size: 18px; line-height: 23px;
  }

  .panel {
    position: absolute; top: 447px; height: 94px; background: var(--panel);
    box-shadow: 0 12px 10px -8px rgba(0,0,0,0.25);
  }
  .connect { left: 120px; width: 228px; text-align: center; }
  .panel-title { font-family: "Signika", sans-serif; font-weight: 700; font-size: 23px; color: #555; }
  .connect .panel-title { margin-top: 17px; }
  .social { display: flex; gap: 7px; justify-content: center; margin-top: 6px; }
  .social span { width: 31px; height: 31px; border-radius: 3px; background: #6f716a; }

  .newsletter { left: 361px; width: 711px; }
  .newsletter .panel-title { text-align: center; margin-top: 10px; }
  .newsletter .panel-title em { font-style: normal; color: var(--green); }
  .subscribe { position: absolute; left: 54px; top: 46px; display: flex; gap: 4px; }
  .email-field {
    width: 501px; height: 38px; border: 1px solid #c8c8c8; border-radius: 3px;
    background: linear-gradient(#ececec, #ffffff); font-size: 14px; padding: 6px 9px; color: #666;
  }
  .btn-subscribe {
    width: 98px; height: 38px; border-radius: 3px; border: 1px solid #8a8a8a;
    background: linear-gradient(#b5b5b5, #7e7e7e); color: var(--white); font-weight: 700; font-size: 16px;
    display: flex; align-items: center; justify-content: center;
  }

  .welcome { position: absolute; left: 123px; top: 580px; width: 950px; }
  .welcome h1 { font-family: "Signika", sans-serif; font-weight: 700; font-size: 26px; color: var(--heading); }
  .welcome h2 { font-size: 16px; font-weight: 700; color: var(--green); margin-top: 15px; margin-left: 2px; }
  .welcome p { font-size: 16px; line-height: 21px; margin-left: 2px; }
  .checks { list-style: none; margin: 13px 0 0 3px; }
  .checks li { display: flex; align-items: center; gap: 11px; font-size: 16px; color: #333; height: 34.5px; }
  .checks svg { flex: none; }
  .closing { margin-top: 13px; }

  .btn-quote {
    position: absolute; left: 919px; top: 831px; width: 157px; height: 40px; border-radius: 3px;
    background: linear-gradient(#6cb52e, var(--green-btn)); border: 1px solid #3c7315;
    color: var(--white); font-weight: 700; font-size: 16px;
    display: flex; align-items: center; justify-content: center;
  }

  .footer {
    position: absolute; left: 0; top: 994px; width: 1200px; height: 119px;
    background: linear-gradient(#a2a2a2, #3a3a3a);
  }
  .footer-nav { position: absolute; left: 123px; top: 32px; display: flex; gap: 14px; list-style: none; color: var(--white); font-size: 17px; font-weight: 600; }
  .copyright { position: absolute; left: 123px; top: 59px; color: var(--green-light); font-size: 17px; }
  .footer .contact-line { position: absolute; right: 124px; top: 33px; color: var(--white); font-size: 18px; }
</style>
</head>
<body>
<div class="canvas">
  <header class="topbar">
    <div class="contact-line">
      <svg width="16" height="12" viewBox="0 0 16 12"><path d="M0 0h16v2l-8 5-8-5z M0 4l8 5 8-5v8H0z"/></svg>
      <span>info@maplebeacon.example</span> <span>|</span>
      <svg width="13" height="13" viewBox="0 0 13 13"><path d="M2 0l3 3-1.5 2a8 8 0 0 0 4.5 4.5L10 8l3 3-2 2C5 13 0 8 0 2z"/></svg>
      <strong>587-555-0142</strong>
    </div>
  </header>

  <section class="hero" role="img" aria-label="Photo of a child with wild hair and glasses shouting with excitement in a grey cardigan"></section>

  <div class="brand-panel">
    <div class="brand"><span class="brand-mark"></span><span class="brand-name">MAPLE BEACON</span></div>
    <div class="brand-tag">Because You're Awesome!</div>
    <ul class="main-nav">
      <li>STRATEGY</li><li>PORTFOLIO</li><li>ABOUT US</li><li>CONTACT US</li><li>BLOG</li>
    </ul>
  </div>

  <ul class="steps">
    <li>MAPLE BEACON</li><li>BE FOUND</li><li class="active">CONNECT</li><li>GET GROWING</li>
  </ul>

  <p class="hero-caption">It's your chance to engage your audience and lead the conversation. It's the new word of mouth</p>

  <section class="panel connect">
    <h3 class="panel-title">CONNECT WITH US</h3>
    <div class="social"><span></span><span></span><span></span><span></span><span></span></div>
  </section>

  <section class="panel newsletter">
    <h3 class="panel-title"><em>GET TIPS AND TRICKS!</em> SUBSCRIBE TO OUR NEWSLETTER</h3>
    <div class="subscribe">
      <div class="email-field">your email id</div>
      <div class="btn-subscribe">Subscribe</div>
    </div>
  </section>

  <main class="welcome">
    <h1>WELCOME TO MAPLE BEACON</h1>
    <h2>Our Mission</h2>
    <p>Etiam adipiscing mollis nulla, ac bibendum elit commodo ac. Pellentesque vehicula sodales vulputate. Suspendisse vel semper tortor. Duis tristique pharetra ligula sed bibendum. Etiam adipiscing mollis nulla, ac bibendum elit commodo ac. Etiam adipiscing mollis nulla, ac bibendum elit commodo ac.</p>
    <ul class="checks">
      <li><svg width="19" height="19" viewBox="0 0 19 19"><rect width="19" height="19" rx="3" fill="#8cc63f"/><path d="M5 10l3 3 6-7" stroke="#fff" stroke-width="2.4" fill="none"/></svg>Nam ac risus metus, sit amet blandit ante.</li>
      <li><svg width="19" height="19" viewBox="0 0 19 19"><rect width="19" height="19" rx="3" fill="#8cc63f"/><path d="M5 10l3 3 6-7" stroke="#fff" stroke-width="2.4" fill="none"/></svg>Nunc adipiscing, ipsum eu scelerisque euismod, diam nisl condimentum neque,</li>
      <li><svg width="19" height="19" viewBox="0 0 19 19"><rect width="19" height="19" rx="3" fill="#8cc63f"/><path d="M5 10l3 3 6-7" stroke="#fff" stroke-width="2.4" fill="none"/></svg>Vel gravida ligula velit vitae nisl. Pellentesque at dignissim ipsum. Vivamus id massa arcu.</li>
      <li><svg width="19" height="19" viewBox="0 0 19 19"><rect width="19" height="19" rx="3" fill="#8cc63f"/><path d="M5 10l3 3 6-7" stroke="#fff" stroke-width="2.4" fill="none"/></svg>Phasellus feugiat condimentum neque ac bibendum.</li>
      <li><svg width="19" height="19" viewBox="0 0 19 19"><rect width="19" height="19" rx="3" fill="#8cc63f"/><path d="M5 10l3 3 6-7" stroke="#fff" stroke-width="2.4" fill="none"/></svg>Pellentesque dictum lectus sapien, eu pulvinar eros.</li>
    </ul>
    <p class="closing">Maecenas lacinia, nulla at interdum dapibus, velit sapien posuere eros, et hendrerit purus erat quis est. Proin commodo blandit mauris sed convallis. Donec tellus metus, feugiat sed condimentum congue, dignissim ut leo.</p>
  </main>

  <div class="btn-quote">Get a Free Quote!</div>

  <footer class="footer">
    <ul class="footer-nav">
      <li>Site Map</li><li>Strategy</li><li>Portfolio</li><li>About Us</li><li>Contact Us</li><li>Blog</li>
    </ul>
    <div class="copyright">©MAPLE BEACON INC. 2013</div>
    <div class="contact-line">
      <svg width="16" height="12" viewBox="0 0 16 12"><path d="M0 0h16v2l-8 5-8-5z M0 4l8 5 8-5v8H0z"/></svg>
      <span>info@maplebeacon.example</span> <span>|</span>
      <svg width="13" height="13" viewBox="0 0 13 13"><path d="M2 0l3 3-1.5 2a8 8 0 0 0 4.5 4.5L10 8l3 3-2 2C5 13 0 8 0 2z"/></svg>
      <strong>587-555-0142</strong>
    </div>
  </footer>
</div>
</body>
</html>
```